Kestrelway Financial Plans

I am looking for a complete resdesign of my small financial presentation. This is a Word Doc/PDF that I print off when meeting with people in private. I often present my "two pager" that I have been using for years and years. It tells them the basics of what I do, how I help people and foundational financial principles.

I have recently gone out on my own in business and have completely rebranded. This presentation is my most used tool, so it is the first of many things I would like to redo. I am hoping it will somehow coordinate with the colors of my business, not necessarily the EXACT same 3 colors everywhere, but have the design colors compliment.

I've uploaded all my logo designs, as well as the current "two-pager". I am not against it going to 3 pages if needed. As it will still land on 2 pages with duplex printing.

It has always been VERY simple. I am wanting it built into a more professional and design specific format, to show off my branding, without being over cluttered.

I am completely open to ANY graphics changes. Obviously some are very novice, the house on the last page has always been overly simplified.

```html
<!DOCTYPE html>
<html lang="en">
<head>
<meta charset="utf-8">
<title>Kestrelway Financial Plans – Client Presentation</title>
<link href="https://fonts.googleapis.com/css2?family=Oswald:wght@400;500;600&family=Montserrat:wght@400;500;600;700;800&display=swap" rel="stylesheet">
<style>
:root{
  --navy:#15202e;
  --green:#1ea33b;
  --grey:#a7a9ac;
  --panel:#ebebeb;
  --line:#d4d5d6;
  --bg:#ececec;
  --white:#ffffff;
  --ink:#232b35;
}
*{margin:0;padding:0;box-sizing:border-box}
html,body{width:1200px;height:633px;overflow:hidden;background:var(--bg)}
body{position:relative;font-family:'Montserrat',sans-serif;color:var(--ink)}
.page{position:absolute;top:78px;width:342px;height:442px;background:var(--white);box-shadow:0 2px 8px rgba(0,0,0,.18);overflow:hidden}
.page--challenge{left:55px}
.page--method{left:429px}
.page--rule{left:801px}
.page svg.art{position:absolute;left:0;top:0;width:342px;height:442px}
.abs{position:absolute}

/* header */
.brand{position:absolute;left:0;top:0;width:132px;height:30px;display:flex;flex-direction:column;align-items:center;justify-content:center;color:var(--navy);font-weight:600;line-height:1}
.brand__name{font-size:14px;letter-spacing:.2px}
.brand__sub{font-size:5px;letter-spacing:1.6px;margin-top:2px}
.page-title{position:absolute;left:132px;top:0;width:210px;height:30px;background:var(--navy);color:var(--white);font-family:'Oswald',sans-serif;font-size:17px;display:flex;align-items:center;justify-content:center;letter-spacing:.2px}

/* challenge columns */
.col-head{position:absolute;top:59px;height:28px;background:var(--navy);color:var(--white);font-weight:700;font-size:9.5px;display:flex;align-items:flex-end;justify-content:center;padding-bottom:3px;letter-spacing:.3px}
.col-body{position:absolute;top:87px;height:111px;background:var(--panel);padding:5px 4px;font-size:4.4px;line-height:1.25}
.stat{display:flex;gap:2px;margin-bottom:2px}
.stat b{font-weight:700;min-width:14px}
.src{font-style:italic;font-size:4.2px;display:block}
.rule-line{border-top:.6px solid var(--grey);margin:4px 0}
.facing{position:absolute;left:84px;top:213px;width:169px;height:29px;background:var(--grey);color:var(--white);font-family:'Oswald',sans-serif;font-size:16px;display:flex;align-items:center;justify-content:center}
.step{position:absolute;width:56px;text-align:center;font-size:5px;font-weight:600;line-height:1.2;color:var(--navy);text-transform:uppercase}
.step--out{font-weight:600;text-transform:none}

/* method page */
.pie-label{position:absolute;font-weight:800;text-align:center;line-height:1.15}
.goal{position:absolute;left:267px;font-size:6px;font-weight:700;color:var(--navy);line-height:1.2;text-transform:uppercase}
.partner{position:absolute;height:34px;border:.8px solid var(--grey);border-radius:2px;display:flex;align-items:center;justify-content:center;gap:3px;font-weight:600;font-size:6.5px;color:var(--navy);text-align:center;line-height:1.1}
.partner i{display:block;width:6px;height:6px;background:var(--green);flex:none}
.pay{position:absolute;left:0;width:342px;top:406px;text-align:center;color:var(--green);font-weight:800;font-size:19px;letter-spacing:.8px}

/* rule of 72 */
.rate{position:absolute;top:47px;height:17px;background:var(--green);color:var(--white);font-weight:700;font-size:7px;padding-left:8px;display:flex;align-items:center}
.rate-body{position:absolute;top:64px;height:99px;background:var(--panel);font-size:5.6px;font-weight:600;color:var(--navy)}
.rate-body table{position:absolute;left:8px;top:7px;width:calc(100% - 12px);border-collapse:collapse}
.rate-body td{height:13.6px;vertical-align:top}
.rate-body td:last-child{text-align:right;font-weight:500}
.doubles{position:absolute;top:177px;width:78px;text-align:center;font-size:5.6px;line-height:1.25;color:var(--navy)}
.doubles b{font-weight:700;display:block}
.roof-title{position:absolute;left:60px;top:256px;width:182px;text-align:center;color:var(--white);font-family:'Oswald',sans-serif;font-size:12px}
.pillar-head{position:absolute;top:282px;height:12px;color:var(--white);font-weight:700;font-size:7px;display:flex;align-items:center;justify-content:center}
.pillar-body{position:absolute;top:294px;height:67px;background:var(--panel);font-size:4.8px;text-align:center;line-height:1.2;color:var(--ink);padding-top:4px}
.pillar-body p{margin-bottom:4.5px}
.pillar-foot{position:absolute;top:361px;height:12px;background:var(--navy);color:var(--green);font-weight:700;font-size:6.2px;display:flex;align-items:center;justify-content:center}
.band{position:absolute;left:13px;width:278px;height:9px;background:var(--green);color:var(--white);font-weight:700;font-size:5.8px;display:flex;align-items:center;justify-content:center;letter-spacing:.3px}
.say-no{position:absolute;left:298px;top:382px;width:40px;text-align:center;color:var(--green);font-weight:700;font-size:5px}
.nojar{position:absolute;left:300px;top:392px;width:36px;height:36px;display:flex;align-items:center;justify-content:center;font-weight:700;font-size:5.5px;color:var(--green)}
</style>
</head>
<body>

<!-- PAGE 1 -->
<section class="page page--challenge">
  <div class="brand"><span class="brand__name">KESTRELWAY</span><span class="brand__sub">FINANCIAL PLANS</span></div>
  <h1 class="page-title">THE FINANCIAL CHALLENGE</h1>

  <div class="col-head" style="left:10px;width:106px">SAVINGS</div>
  <div class="col-head" style="left:118px;width:106px">DEBT</div>
  <div class="col-head" style="left:227px;width:106px">INSURANCE</div>

  <div class="col-body" style="left:10px;width:106px">
    <div class="stat"><b>49%</b><span>of Canadian Employees are living paycheque to paycheque.</span></div>
    <div class="stat"><b>25%</b><span>Canadians are unable to cover an unexpected $500 expense.<span class="src">National Stats Bureau (Feb 2023)</span></span></div>
    <div class="rule-line"></div>
    <div class="stat"><b>25%</b><span>of Canadians need to access their retirement savings early.</span></div>
    <div class="stat"><b>20%</b><span>Canadians have no saving</span></div>
    <div class="stat"><b>39%</b><span>of Canadians aged 55-65 have less than $5,000 in savings.<span class="src">Federal Savings Review (June 2023)</span></span></div>
  </div>
  <div class="col-body" style="left:118px;width:106px">
    <p>The average Canadian has $22,131 in consumer debts, which excludes mortgages.<span class="src">Ledgerline Credit (Aug 2024)</span></p>
    <div class="rule-line"></div>
    <p>Over 55% of Canadians hold credit card debt and the total Canadian household debt has increased to $2.52 trillion, including consumer credit, mortgage and non-mortgage loans.<span class="src">Northern Lenders Assoc (Aug 2024)</span></p>
  </div>
  <div class="col-body" style="left:227px;width:106px">
    <div class="stat"><b>49%</b><span>of Canadians do not have individual life insurance coverage, but</span></div>
    <div class="stat"><b>48%</b><span>say their families would face financial trouble within 6 months of losing someone.<span class="src">Corvane Research (Apr 2023)</span></span></div>
    <div class="rule-line"></div>
    <p>2-in-5 Canadians (43% Women / 44% Men) will be diagnosed with a form of cancer or other critical illness during their lifetime. Every 7 seconds.<span class="src">Wellstat Data Hub (June 2024)</span></p>
  </div>

  <div class="facing">FACING THE CHALLENGE</div>

  <svg class="art" viewBox="0 0 342 442" aria-hidden="true">
    <!-- column icons -->
    <g fill="var(--green)">
      <circle cx="63" cy="56" r="14"/><circle cx="171" cy="56" r="14"/><circle cx="280" cy="56" r="14"/>
    </g>
    <g fill="none" stroke="#fff" stroke-width="1.3">
      <ellipse cx="63" cy="57" rx="6" ry="4.5" fill="#fff" stroke="none"/>
      <rect x="164" y="51" width="14" height="10" rx="1"/><line x1="164" y1="55" x2="178" y2="55"/><line x1="163" y1="62" x2="179" y2="50"/>
      <path d="M272 57 A8 8 0 0 1 288 57 Z" fill="#fff" stroke="none"/><path d="M280 57 V64 a1.5 1.5 0 0 1 -3 0"/>
    </g>
    <!-- step rings -->
    <g>
      <circle cx="40" cy="284" r="30" fill="var(--navy)"/>
      <circle cx="92" cy="284" r="30" fill="var(--green)"/>
      <circle cx="145" cy="284" r="30" fill="var(--grey)"/>
      <circle cx="198" cy="284" r="30" fill="var(--navy)"/>
      <circle cx="251" cy="284" r="30" fill="var(--green)"/>
      <circle cx="303" cy="284" r="30" fill="var(--grey)"/>
    </g>
    <g fill="#fff" stroke="var(--line)" stroke-width="1.5">
      <circle cx="40" cy="284" r="20"/><circle cx="92" cy="284" r="20"/><circle cx="145" cy="284" r="20"/>
      <circle cx="198" cy="284" r="20"/><circle cx="251" cy="284" r="20"/><circle cx="303" cy="284" r="20"/>
    </g>
    <g fill="none" stroke="var(--green)" stroke-width="1.4">
      <rect x="31" y="279" width="18" height="10" rx="1"/><circle cx="40" cy="284" r="2.5"/>
      <path d="M83 283 A9 9 0 0 1 101 283 Z" fill="var(--green)" stroke="none"/><path d="M92 283 V292 a2 2 0 0 1 -4 0"/>
      <rect x="136" y="278" width="18" height="12" rx="1"/><line x1="136" y1="282" x2="154" y2="282"/><line x1="134" y1="292" x2="156" y2="276"/>
      <rect x="188" y="278" width="12" height="10" fill="var(--green)" stroke="none"/><path d="M200 281 h5 l3 4 v3 h-8 Z" fill="var(--green)" stroke="none"/><circle cx="192" cy="290" r="2" fill="#fff"/><circle cx="204" cy="290" r="2" fill="#fff"/>
      <ellipse cx="251" cy="285" rx="9" ry="7" fill="var(--green)" stroke="none"/>
      <rect x="294" y="276" width="18" height="16" rx="1"/><rect x="298" y="280" width="10" height="8"/>
    </g>
    <!-- dotted connectors and arrows -->
    <g stroke="var(--navy)" stroke-width="1.6" stroke-dasharray="1.4 1.8">
      <line x1="40" y1="340" x2="40" y2="377"/><line x1="92" y1="340" x2="92" y2="377"/><line x1="145" y1="340" x2="145" y2="377"/>
      <line x1="198" y1="340" x2="198" y2="377"/><line x1="251" y1="340" x2="251" y2="377"/><line x1="303" y1="340" x2="303" y2="377"/>
    </g>
    <g fill="var(--green)">
      <path d="M38 398h4v4h3l-5 5-5-5h3z"/><path d="M90 398h4v4h3l-5 5-5-5h3z"/><path d="M143 398h4v4h3l-5 5-5-5h3z"/>
      <path d="M196 398h4v4h3l-5 5-5-5h3z"/><path d="M301 398h4v4h3l-5 5-5-5h3z"/>
    </g>
  </svg>

  <div class="step" style="left:12px;top:322px">Cash Flow</div>
  <div class="step" style="left:64px;top:318px">Cash Flow Protection</div>
  <div class="step" style="left:117px;top:318px">Debt Management</div>
  <div class="step" style="left:170px;top:318px">Emergency Fund</div>
  <div class="step" style="left:223px;top:318px">Build Wealth</div>
  <div class="step" style="left:275px;top:318px">Preserve Wealth</div>

  <div class="step" style="left:12px;top:387px">Analyze</div>
  <div class="step" style="left:64px;top:383px">Income Protection</div>
  <div class="step" style="left:117px;top:387px">20%</div>
  <div class="step" style="left:170px;top:387px">If / When</div>
  <div class="step" style="left:219px;top:384px;width:64px">Financial Independence Number (FIN)</div>
  <div class="step" style="left:275px;top:384px">Leaving a Legacy</div>

  <div class="step step--out" style="left:12px;top:409px">Free Up<br>$400-$600</div>
  <div class="step step--out" style="left:60px;top:409px;width:64px">Life Insurance<br>CI/DI Insurance</div>
  <div class="step step--out" style="left:117px;top:411px">6-7%</div>
  <div class="step step--out" style="left:170px;top:411px">3-6 Months</div>
  <div class="step step--out" style="left:275px;top:411px">Will Prep</div>
</section>

<!-- PAGE 2 -->
<section class="page page--method">
  <div class="brand"><span class="brand__name">KESTRELWAY</span><span class="brand__sub">FINANCIAL PLANS</span></div>
  <h1 class="page-title">HOW AM I DOING IT</h1>

  <svg class="art" viewBox="0 0 342 442" aria-hidden="true">
    <circle cx="138" cy="152" r="101" fill="#e4e5e6"/>
    <path d="M138 59 A93 93 0 0 0 138 245 Z" fill="var(--green)"/>
    <path d="M138 152 L138 59 A93 93 0 0 1 231 152 Z" fill="var(--navy)"/>
    <path d="M138 152 L231 152 A93 93 0 0 1 138 245 Z" fill="var(--grey)"/>
    <circle cx="138" cy="152" r="36" fill="#fff" stroke="#c9cacc" stroke-width="3"/>
    <ellipse cx="140" cy="139" rx="11" ry="8" fill="var(--navy)"/>
    <rect x="133" y="145" width="3" height="5" fill="var(--navy)"/><rect x="143" y="145" width="3" height="5" fill="var(--navy)"/>
    <!-- money icon -->
    <g fill="none" stroke="#fff" stroke-width="1.4"><rect x="61" y="125" width="20" height="11" rx="1"/><circle cx="71" cy="130.5" r="2.5"/><path d="M64 122 l15 -3"/></g>
    <!-- tax doc icon -->
    <g fill="none" stroke="var(--green)" stroke-width="1.3"><rect x="182" y="90" width="14" height="17"/><line x1="185" y1="100" x2="193" y2="100"/><line x1="185" y1="103" x2="193" y2="103"/></g>
    <!-- debt card icon -->
    <g fill="none" stroke="var(--navy)" stroke-width="1.4"><rect x="173" y="191" width="18" height="12" rx="1"/><line x1="173" y1="195" x2="191" y2="195"/><line x1="171" y1="205" x2="193" y2="189"/></g>
    <!-- bracket -->
    <g stroke="var(--grey)" stroke-width="1" fill="none">
      <line x1="234" y1="147" x2="241" y2="147"/>
      <line x1="241" y1="77" x2="241" y2="229"/>
      <line x1="241" y1="77" x2="262" y2="77"/><line x1="241" y1="124" x2="262" y2="124"/>
      <line x1="241" y1="179" x2="262" y2="179"/><line x1="241" y1="229" x2="262" y2="229"/>
    </g>
    <path d="M336 -0" />
    <path d="M156 388h4v7h3l-5 6-5-6h3z" fill="var(--navy)"/>
  </svg>

  <div class="pie-label" style="left:40px;top:142px;width:64px;color:#fff;font-size:9px">LIVING<br>EXPENSES</div>
  <div class="pie-label" style="left:164px;top:112px;width:50px;color:var(--green);font-size:9px">TAXES</div>
  <div class="pie-label" style="left:102px;top:155px;width:74px;color:var(--navy);font-size:9.5px">SAVINGS</div>
  <div class="pie-label" style="left:157px;top:207px;width:50px;color:var(--navy);font-size:9px">DEBT</div>

  <div class="goal" style="top:71px">Retirement<br>Savings</div>
  <div class="goal" style="top:117px">Children's<br>Education</div>
  <div class="goal" style="top:172px">Proper<br>Protection</div>
  <div class="goal" style="top:222px">Freedom<br>From Debt</div>

  <div class="partner" style="left:59px;top:267px;width:69px"><i></i>Marrowind</div>
  <div class="partner" style="left:134px;top:267px;width:69px">Larchfield Life</div>
  <div class="partner" style="left:209px;top:267px;width:69px">Solace Mutual</div>
  <div class="partner" style="left:25px;top:307px;width:69px">Tundra Cover Plan</div>
  <div class="partner" style="left:99px;top:307px;width:69px">Alderan Group</div>
  <div class="partner" style="left:174px;top:307px;width:70px"><i></i>Harbourline<br>Insurance</div>
  <div class="partner" style="left:251px;top:307px;width:69px">Quillan Wealth</div>
  <div class="partner" style="left:65px;top:346px;width:69px">Brookmere Insurance</div>
  <div class="partner" style="left:140px;top:346px;width:70px;font-size:10px">Vellora</div>
  <div class="partner" style="left:215px;top:346px;width:70px">Fairhold Life</div>

  <div class="pay">PAY US</div>
</section>

<!-- PAGE 3 -->
<section class="page page--rule">
  <div class="brand"><span class="brand__name">KESTRELWAY</span><span class="brand__sub">FINANCIAL PLANS</span></div>
  <h1 class="page-title">RULE OF 72</h1>

  <div class="rate" style="left:11px;width:78px">AGE</div>
  <div class="rate" style="left:92px;width:78px">AGE</div>
  <div class="rate" style="left:174px;width:78px">AGE</div>
  <div class="rate" style="left:256px;width:78px">AGE</div>

  <div class="rate-body" style="left:11px;width:78px"><table>
    <tr><td>29</td><td>$10,000</td></tr><tr><td>47</td><td>$20,000</td></tr><tr><td>65</td><td>$40,000</td></tr></table></div>
  <div class="rate-body" style="left:92px;width:78px"><table>
    <tr><td>29</td><td>$10,000</td></tr><tr><td>41</td><td>$20,000</td></tr><tr><td>53</td><td>$40,000</td></tr><tr><td>65</td><td>$80,000</td></tr></table></div>
  <div class="rate-body" style="left:174px;width:78px"><table>
    <tr><td>29</td><td>$10,000</td></tr><tr><td>38</td><td>$20,000</td></tr><tr><td>47</td><td>$40,000</td></tr><tr><td>56</td><td>$80,000</td></tr><tr><td>65</td><td>$160,000</td></tr></table></div>
  <div class="rate-body" style="left:256px;width:78px"><table>
    <tr><td>29</td><td>$10,000</td></tr><tr><td>35</td><td>$20,000</td></tr><tr><td>41</td><td>$40,000</td></tr><tr><td>47</td><td>$80,000</td></tr><tr><td>53</td><td>$160,000</td></tr><tr><td>59</td><td>$320,000</td></tr><tr><td>65</td><td>$640,000</td></tr></table></div>

  <svg class="art" viewBox="0 0 342 442" aria-hidden="true">
    <g fill="var(--navy)">
      <circle cx="71" cy="55" r="12"/><circle cx="153" cy="55" r="12"/><circle cx="235" cy="55" r="12"/><circle cx="317" cy="55" r="12"/>
    </g>
    <g fill="var(--green)" font-family="Montserrat,sans-serif" font-weight="700" font-size="8" text-anchor="middle">
      <text x="71" y="58">4%</text><text x="153" y="58">6%</text><text x="235" y="58">8%</text><text x="317" y="58">12%</text>
    </g>
    <g fill="var(--green)">
      <rect x="11" y="163" width="78" height="2"/><rect x="92" y="163" width="78" height="2"/><rect x="174" y="163" width="78" height="2"/><rect x="256" y="163" width="78" height="2"/>
      <path d="M45 165h10l-5 5z"/><path d="M126 165h10l-5 5z"/><path d="M208 165h10l-5 5z"/><path d="M290 165h10l-5 5z"/>
    </g>
    <!-- roof -->
    <path d="M150 216 L297 274 L6 274 Z" fill="var(--navy)"/>
    <circle cx="150" cy="224" r="5" fill="var(--green)"/>
    <path d="M140 248 C148 244 149 236 150 229 C151 236 152 244 160 248" fill="none" stroke="#fff" stroke-width=".8"/>
    <rect x="6" y="275" width="291" height="4" fill="var(--green)"/>
    <!-- pillar heads -->
    <g fill="var(--navy)">
      <path d="M7 282h69l-2 12h-65z"/><path d="M81 282h68l-2 12h-64z"/><path d="M154 282h71l-2 12h-67z"/><path d="M228 282h71l-2 12h-67z"/>
    </g>
    <!-- no sign -->
    <circle cx="318" cy="410" r="17" fill="none" stroke="var(--green)" stroke-width="2"/>
    <line x1="306" y1="422" x2="330" y2="398" stroke="var(--green)" stroke-width="2"/>
  </svg>

  <div class="doubles" style="left:11px">Money Doubles<b>EVERY 18 YEARS</b></div>
  <div class="doubles" style="left:92px">Money Doubles<b>EVERY 12 YEARS</b></div>
  <div class="doubles" style="left:174px">Money Doubles<b>EVERY 9 YEARS</b></div>
  <div class="doubles" style="left:256px">Money Doubles<b>EVERY 6 YEARS</b></div>

  <div class="roof-title">WEALTH BUILDING</div>

  <div class="pillar-head" style="left:9px;width:65px">HOME</div>
  <div class="pillar-head" style="left:83px;width:64px">RRSP</div>
  <div class="pillar-head" style="left:156px;width:67px">TFSA</div>
  <div class="pillar-head" style="left:230px;width:67px">PERM LIFE</div>

  <div class="pillar-body" style="left:9px;width:65px"><p>Partner with Mortgage Brokers for Best Rates</p><p>Mortgage Insurance Alternatives</p></div>
  <div class="pillar-body" style="left:83px;width:64px"><p>Tax Deduction</p><p>Tax Deferred</p></div>
  <div class="pillar-body" style="left:156px;width:67px"><p>No Tax Deduction</p><p>Tax Free Growth</p><p>2009 - $95,000</p><p>Limit 2023<br>$7,000/Yr</p></div>
  <div class="pillar-body" style="left:230px;width:67px"><p>No Tax Deduction</p><p>Qualify</p><p>Tax Deferred Growth</p></div>

  <div class="pillar-foot" style="left:9px;width:65px">SELL</div>
  <div class="pillar-foot" style="left:83px;width:64px">100% TAX</div>
  <div class="pillar-foot" style="left:156px;width:67px">0% TAX</div>
  <div class="pillar-foot" style="left:230px;width:67px">0% TAX</div>

  <div class="band" style="top:378px">EMERGENCY/OPPORTUNITY FUNDING</div>
  <div class="band" style="top:390px">DEBT MANAGEMENT</div>
  <div class="band" style="top:403px">CASHFLOW PROTECTION</div>
  <div class="band" style="top:415px">LIFE/CRITICAL ILLNESS/DISSABILITY</div>

  <div class="say-no">SAY NO TO</div>
  <div class="nojar">pitchjar</div>
</section>

</body>
</html>
```